Web Developer Needs a Business Card Design

I need a personal business card design that represents me as a web developer for potential employers. I would like the background to be a dark color on the front for contrast with my logo and name. The back will have all my information along with a smaller version of the logo. I want something with a modern look and feel, not too conservative. This will be used for potential employers and freelance work.

Industry/Entity Type

Business

Contact Information for Business Card

Front should have my logo and name. The back should have all my personal information which would include: name: Tom Varulek, phone: 570-614-3098, email: tomvarulek@quillbox.net, website url: www.tomvarulek.net, logo, web developer.

Font styles to use
Sans Serif

Requirements
Must have
• Must include my logo. The color palette base color will be the logo color.

```html
<!DOCTYPE html>
<html lang="en">
<head>
<meta charset="utf-8">
<title>Tom Varulek — Business Card</title>
<link rel="stylesheet" href="https://fonts.googleapis.com/css2?family=Open+Sans:wght@400;700&display=swap">
<style>
  :root {
    --teal: #6cc7b5;
    --grey: #8a8a8a;
    --text-grey: #5e5e5e;
    --charcoal: #2b2b2b;
    --white: #ffffff;
    --backdrop: #ecebe8;
  }
  * { margin: 0; padding: 0; box-sizing: border-box; }
  html, body {
    width: 1200px; height: 900px; overflow: hidden;
    background: var(--backdrop);
    font-family: "Open Sans", sans-serif;
  }
  .stage { position: relative; width: 1200px; height: 900px; }
  .card {
    position: absolute; width: 600px; height: 343px; overflow: hidden;
    box-shadow: 0 6px 18px rgba(0,0,0,0.18);
  }

  /* Front */
  .card-front { left: 540px; top: 80px; background: var(--charcoal); }
  .front-ring {
    position: absolute; left: 60px; top: -60px; width: 480px; height: 463px;
    border: 24px solid var(--white); border-radius: 50%;
  }
  .front-identity {
    position: absolute; left: 0; right: 0; top: 128px; text-align: center; color: var(--white);
  }
  .front-name { font-weight: 700; font-size: 30px; line-height: 1.15; }
  .front-title { font-weight: 400; font-size: 32px; line-height: 1.25; white-space: nowrap; }

  /* Back */
  .card-back { left: 60px; top: 470px; background: var(--white); }
  .back-decor { position: absolute; inset: 0; }
  .back-identity { position: absolute; left: 72px; top: 22px; }
  .back-name { color: var(--teal); font-weight: 700; font-size: 19px; line-height: 1.2; }
  .back-title { color: var(--text-grey); font-size: 15px; line-height: 1.2; }

  .contact-list { position: absolute; left: 26px; top: 168px; list-style: none; }
  .contact-item {
    display: flex; align-items: center; gap: 9px;
    color: var(--text-grey); font-size: 16px; line-height: 23px;
  }
  .contact-icon { width: 12px; height: 12px; fill: var(--teal); flex: none; }

  .brand-mark {
    position: absolute; left: 340px; top: 110px;
    display: flex; align-items: center; gap: 12px;
  }
  .brand-dot {
    width: 46px; height: 46px; border-radius: 50%;
    border: 7px solid var(--teal); flex: none;
  }
  .brand-name { color: var(--teal); font-weight: 700; font-size: 26px; white-space: nowrap; }
</style>
</head>
<body>
<main class="stage">

  <section class="card card-front" aria-label="Card front">
    <div class="front-ring"></div>
    <div class="front-identity">
      <p class="front-name">Tom Varulek</p>
      <p class="front-title">Front-End Developer</p>
    </div>
  </section>

  <section class="card card-back" aria-label="Card back">
    <svg class="back-decor" width="600" height="343" viewBox="0 0 600 343" aria-hidden="true">
      <polygon points="0,22 18,22 12,44 0,44" fill="var(--grey)"/>
      <polygon points="24,22 62,22 56,44 16,44" fill="var(--teal)"/>
      <polygon points="0,268 300,268 286,296 0,296" fill="var(--grey)"/>
      <polygon points="296,296 600,296 600,343 272,343" fill="var(--teal)"/>
    </svg>

    <div class="back-identity">
      <p class="back-name">Tom Varulek</p>
      <p class="back-title">Front-End Developer</p>
    </div>

    <ul class="contact-list">
      <li class="contact-item">
        <svg class="contact-icon" viewBox="0 0 24 24" aria-hidden="true"><path d="M6.6 10.8a15.1 15.1 0 0 0 6.6 6.6l2.2-2.2a1 1 0 0 1 1-.25 11.4 11.4 0 0 0 3.6.57 1 1 0 0 1 1 1V20a1 1 0 0 1-1 1A17 17 0 0 1 3 4a1 1 0 0 1 1-1h3.5a1 1 0 0 1 1 1c0 1.25.2 2.45.57 3.57a1 1 0 0 1-.25 1z"/></svg>
        570-614-3098
      </li>
      <li class="contact-item">
        <svg class="contact-icon" viewBox="0 0 24 24" aria-hidden="true"><path d="M2 5h20v14H2z M2 5l10 8 10-8" stroke="var(--white)" stroke-width="1.5"/></svg>
        tomvarulek@quillbox.net
      </li>
      <li class="contact-item">
        <svg class="contact-icon" viewBox="0 0 24 24" aria-hidden="true"><circle cx="12" cy="12" r="10"/><path d="M2 12h20M12 2c3 3 3 17 0 20M12 2c-3 3-3 17 0 20" stroke="var(--white)" stroke-width="1.4" fill="none"/></svg>
        www.tomvarulek.net
      </li>
    </ul>

    <div class="brand-mark">
      <span class="brand-dot"></span>
      <span class="brand-name">Tom Varulek</span>
    </div>
  </section>

</main>
</body>
</html>
```